Web Design for Independent Pet Supply shop.

Larch Critter Depot is a locally owned and operated premium natural pet food store and supply company with 2 thriving retail stores in Bend, Oregon, and a home delivery service. The pet food offered is the best on the market and may be described as “holistic”. Also on offer is a vast selection of toys, training tools, treats, and other supplies, as well as dog washing services that range from "do-it yourself" to "spa." Current site: LarchCritterDepot.com. They need a new, updated and responsive site.
Likes:
Tovanels.com: Natural colors, not loud, pages in motion, simple & clean but very informative.
Dorvikmerin.com: Everything in simple big colorful blocks. The specials run across the top and in motion. This site looks very professional but simple. The information is available several different places.
Plenharvest.com: Again big blocks through out. Very Fun and inviting. Tons of information with videos and recipes and testimonials. Pleasant feel and colors as well.
Dislikes:
Furlix.com: Looks cheap, hate the colors, very busy and over whelming. Hate the old style header bar going across with options. Too many printed words instead of fun images.
Colors should be "natural" tones, warm and soothing. Deep dark blue and greys with earthy wood color.
Do Not Use: Blue violet, violet, red violet

```html
<!DOCTYPE html>
<html lang="en">
<head>
<meta charset="utf-8">
<title>Larch Critter Depot</title>
<link rel="stylesheet" href="https://fonts.googleapis.com/css2?family=Open+Sans:wght@400;600;700&display=swap">
<style>
:root{
  --navy:#0b2d50;
  --navy-deep:#072441;
  --navy-card:#0e3a66;
  --nav:#03305a;
  --nav-active:#0b4a80;
  --wood:#a9772f;
  --sage:#9aa83a;
  --blue-link:#1a6fb5;
  --ink:#3b3b3b;
  --muted:#8a8a8a;
  --paper:#ffffff;
  --mist:#f2f2f2;
  --footer:#3a3a3a;
  --footer-text:#d8d8d8;
}
*{box-sizing:border-box;margin:0;padding:0}
html,body{width:1200px;height:2490px;overflow:hidden;background:var(--paper);font-family:"Open Sans",Arial,sans-serif;color:var(--ink)}
.page{position:relative;width:1200px;height:2490px}
.abs{position:absolute}

.site-header{left:0;top:0;width:1200px;height:105px;background:var(--paper)}
.brand{left:100px;top:32px;display:flex;align-items:center;gap:12px;font-size:30px;font-weight:700;color:var(--wood);letter-spacing:.5px;white-space:nowrap}
.brand-dot{width:34px;height:34px;border-radius:50%;background:var(--wood)}
.partner{left:598px;top:38px;display:flex;align-items:center;gap:7px;font-size:15px;font-weight:700;color:var(--sage);white-space:nowrap}
.partner-dot{width:12px;height:12px;border-radius:50%;background:var(--sage)}
.call-icon{left:785px;top:20px;width:62px;height:62px;border:2px solid var(--blue-link);border-radius:50%;display:flex;align-items:center;justify-content:center}
.call-label{left:868px;top:24px;font-size:22px;color:var(--blue-link)}
.call-numbers{left:868px;top:54px;font-size:17px;color:var(--blue-link);white-space:nowrap}

.main-nav{left:0;top:105px;width:1200px;height:72px;background:var(--nav)}
.main-nav ul{list-style:none;display:flex;height:72px;margin-left:98px}
.main-nav li{height:72px;display:flex;align-items:center;padding:0 27px;color:#fff;font-size:14.5px;white-space:nowrap}
.main-nav li.active{background:var(--nav-active);padding:0 40px}

.hero{left:0;top:177px;width:1200px;height:596px;background:radial-gradient(ellipse at 55% 35%,#c98a2c 0%,#a8621c 40%,#6a3a12 75%,#3d2510 100%)}
.hero-title{left:98px;top:48px;font-size:78px;line-height:104px;font-weight:600;letter-spacing:5px;color:transparent;-webkit-text-stroke:2px #fff;white-space:nowrap}
.hero-dots{left:568px;top:528px;display:flex;gap:12px}
.hero-dots span{width:13px;height:13px;border-radius:50%;background:#3a3a2a}
.hero-dots span.on{background:#2a8de0}

.features{left:0;top:773px;width:1200px;height:273px;background:var(--navy)}
.feature{position:absolute;top:0;width:342px;height:273px;padding:30px 0 0 0;color:#fff}
.feature.highlight{top:-4px;height:274px;background:var(--navy-card);border-bottom:4px solid #e8eef5}
.feature-head{display:flex;align-items:center;gap:18px}
.feature-icon{flex:none;width:68px;height:68px;border:2px solid #fff;border-radius:50%;display:flex;align-items:center;justify-content:center}
.feature h3{font-size:26px;font-weight:600;white-space:nowrap}
.feature p{margin-top:24px;font-size:12.3px;line-height:21px;text-align:justify}
.feature .more{margin-top:14px;text-align:right;font-size:12px}

.welcome{left:0;top:1046px;width:1200px;height:377px;background:linear-gradient(180deg,#f6ece6,#efe0d6 50%,#f3e6dc)}
.welcome h2{position:absolute;left:0;width:1200px;top:58px;text-align:center;font-size:27px;font-weight:600;color:#4a4a4a}
.welcome p{position:absolute;left:198px;width:804px;top:124px;text-align:center;font-size:11.6px;line-height:20px;color:#5a5a5a}
.btn-more{left:492px;top:252px;width:153px;height:54px;border-radius:6px;background:var(--navy);color:#fff;font-size:17px;font-weight:600;display:flex;align-items:center;justify-content:center}

.news{left:0;top:1423px;width:1200px;height:560px;background:var(--mist)}
.news h2{position:absolute;left:0;width:1200px;top:70px;text-align:center;font-size:26px;font-weight:600;color:var(--navy-deep)}
.news p{position:absolute;left:118px;width:964px;top:135px;text-align:center;font-size:11.6px;line-height:21px;color:var(--muted)}
.news p b{color:var(--navy);font-weight:600}
.dog-photo{left:0;top:262px;width:1200px;height:298px;background:linear-gradient(180deg,rgba(242,242,242,0) 0%,#b99a78 45%,#5e4632 100%);clip-path:polygon(0 30%,30% 0,60% 5%,100% 15%,100% 100%,0 100%)}

.newsletter{left:0;top:1983px;width:1200px;height:200px;background:var(--navy)}
.newsletter h3{position:absolute;left:208px;top:70px;color:#fff;font-size:24px;font-weight:600}
.newsletter .sub{position:absolute;left:208px;top:108px;color:#fff;font-size:17px}
.mail-field{left:625px;top:80px;width:303px;height:54px;background:#7f94a8;border-radius:6px 0 0 6px;color:#fff;font-size:12px;display:flex;align-items:center;padding-left:24px}
.mail-btn{left:928px;top:80px;width:173px;height:54px;background:#0a3560;border-radius:0 6px 6px 0;color:#fff;font-size:17px;display:flex;align-items:center;justify-content:center}

.site-footer{left:0;top:2183px;width:1200px;height:307px;background:var(--footer)}
.footer-links{position:absolute;left:0;width:1200px;top:77px;display:flex;justify-content:center;gap:48px;color:var(--footer-text);font-size:13px}
.footer-links span::before{content:"";display:inline-block;width:10px;height:10px;border-radius:50%;background:#1b4a7a;margin-right:12px}
.socials{position:absolute;left:392px;top:140px;display:flex;gap:20px}
.socials span{width:50px;height:50px;border-radius:4px}
.footer-partner{position:absolute;left:678px;top:140px;width:130px;height:50px;border:1px solid #666;display:flex;align-items:center;justify-content:center;color:#bbb;font-size:13px;font-weight:600;white-space:nowrap}
.copyright{position:absolute;left:0;width:1200px;top:229px;text-align:center;color:#9a9a9a;font-size:12.5px}
</style>
</head>
<body>
<div class="page">

  <header class="site-header abs">
    <div class="brand abs"><span class="brand-dot"></span>Larch Critter Depot</div>
    <div class="partner abs"><span class="partner-dot"></span>Kindle Pet Pantry</div>
    <div class="call-icon abs">
      <svg width="26" height="26" viewBox="0 0 24 24"><path d="M6.6 10.8a15 15 0 0 0 6.6 6.6l2.2-2.2c.3-.3.7-.4 1-.2 1.1.4 2.3.6 3.6.6.6 0 1 .4 1 1V20c0 .6-.4 1-1 1A17 17 0 0 1 3 4c0-.6.4-1 1-1h3.5c.6 0 1 .4 1 1 0 1.3.2 2.5.6 3.6.1.3 0 .7-.2 1z" fill="#1a6fb5"/></svg>
    </div>
    <div class="call-label abs">Call Us :</div>
    <div class="call-numbers abs">541-555-0142 / 541-555-0187</div>
  </header>

  <nav class="main-nav abs">
    <ul>
      <li class="active">Home</li><li>Events</li><li>Blog</li><li>About</li><li>Dog Wash</li><li>Products</li><li>Resources</li><li>Links</li><li>Contact Us</li>
    </ul>
  </nav>

  <section class="hero abs" role="img" aria-label="Two dogs resting in a pile of autumn leaves in a forest">
    <div class="hero-title abs">LARCH CRITTER<br>DEPOT</div>
    <div class="hero-dots abs"><span></span><span class="on"></span><span></span></div>
  </section>

  <section class="features abs">
    <div class="feature" style="left:98px;width:312px">
      <div class="feature-head">
        <div class="feature-icon"><svg width="34" height="34" viewBox="0 0 34 34" fill="#fff"><circle cx="9" cy="13" r="3.5"/><circle cx="14" cy="7" r="3.5"/><circle cx="21" cy="7" r="3.5"/><circle cx="26" cy="13" r="3.5"/><ellipse cx="17.5" cy="22" rx="7" ry="6"/></svg></div>
        <h3>Pup Brew</h3>
      </div>
      <p>Now you can pour some cold brew for your pup in a fun and easy way that has a delicious flavor and packed full of vegetarian K9 specific glucosamine with essential vitamins and minerals for your dogs</p>
      <div class="more">[ Read More ]</div>
    </div>
    <div class="feature highlight" style="left:428px;padding-left:25px;padding-right:20px">
      <div class="feature-head">
        <div class="feature-icon"><svg width="34" height="30" viewBox="0 0 34 30" fill="#fff"><path d="M4 20h26l-3 7H7z"/><path d="M8 18a9 9 0 0 1 18 0z"/></svg></div>
        <h3>Marlow Recall</h3>
      </div>
      <p>Now you can pour some cold brew for your pup in a fun and easy way that has a delicious flavor and packed full of vegetarian K9 specific glucosamine with essential vitamins and minerals for your dogs</p>
      <div class="more">[ Read More ]</div>
    </div>
    <div class="feature" style="left:803px;width:298px">
      <div class="feature-head">
        <div class="feature-icon"><svg width="30" height="34" viewBox="0 0 30 34" fill="none" stroke="#fff" stroke-width="2.5"><circle cx="15" cy="13" r="10"/><circle cx="15" cy="13" r="4" fill="#fff"/><path d="M9 21l-3 11 9-4 9 4-3-11"/></svg></div>
        <h3>Tallwater</h3>
      </div>
      <p>Now you can pour some cold brew for your pup in a fun and easy way that has a delicious flavor and packed full of vegetarian K9 specific glucosamine with essential vitamins and minerals for your dogs</p>
      <div class="more">[ Read More ]</div>
    </div>
  </section>

  <section class="welcome abs" role="img" aria-label="Faded background of colorful kibble pieces">
    <h2>WELCOME TO LARCH CRITTER DEPOT</h2>
    <p>At vero eos et accusamus et iusto odio dignissimos ducimus qui blanditiis praesentium voluptatum deleniti atque corrupti quos dolores et quas molestias excepturi sint occaecati cupiditate non provident, similique sunt in culpa qui officia deserunt mollitia animi, id est laborum et dolorum fuga. Et harum quidem rerum facilis est et expedita distinctio. Nam libero tempore, cum soluta nobis est eligendi optio cumque nihil impedit Nam libero tempore, cum soluta nobis est eligendi optio cumque nihil impedit&nbsp; Nam libero tempore, cum soluta nobis</p>
    <div class="btn-more abs">Read More</div>
  </section>

  <section class="news abs">
    <h2>THE LARCH CRITTER DEPOT DOG WASH NEWS AND UPDATES</h2>
    <p>The Larch Critter Depot Dog Wash attendants are always here to help wash your four-legged friends, and trim their nails…but they are also here to help educate all of us! Nail trims are such an essential routine for our pups, especially if they don’t run and walk as much as they would in the wild. Below are two photo that demonstrate how important nail trims are. The ‘Before’ shot shows the dogs two front feet. Looking at the photo the left foot ( Dogs right foot) has not been trimmed yet. Notice the two outside toes twisting out and away from the foot. The right foot ( Dogs left foot ) has already been trimmed. Notice how “cat like” the toes are, tight and together allowing&nbsp; <b>[ Read More ]</b></p>
    <div class="dog-photo abs" role="img" aria-label="A row of puppies of different breeds sitting together"></div>
  </section>

  <section class="newsletter abs">
    <h3>SIGN UP FOR NEWS LETTER</h3>
    <div class="sub">The Larch Critter Depot Dog Wash attendants</div>
    <div class="mail-field abs">ENTER THE MAIL ID</div>
    <div class="mail-btn abs">SUBSCRIBE</div>
  </section>

  <footer class="site-footer abs">
    <div class="footer-links"><span>CONTACT</span><span>RETURN POLICY</span><span>PRIVACY POLICY</span><span>EMPLOYMENT</span><span>STAFF LOGIN</span></div>
    <div class="socials" aria-label="Social links">
      <span style="background:#c8412f"></span><span style="background:#2a8fd0"></span><span style="background:#2f5597"></span><span style="background:#2c5c86"></span>
    </div>
    <div class="footer-partner">Kindle Pet Pantry</div>
    <div class="copyright">COPYRIGHTS@2015 LARCH CRITTER DEPOT 2015. ALL RIGHTS RESERVED</div>
  </footer>

</div>
</body>
</html>
```